Innovative Event Ticketing Start Up. Needs a Web Design

We need a web design for a new company based in London called 'Bandwise'. We are a platform which facilitates the building of groups of customers for events. As more people commit to an event, the price incrementally decreases. We would like there to be an emphasis on the sharing element and the decreasing price with higher participation.

Any quieres please email me at rvkm47@postlane.net

Target Market(s)

18-30 year olds who are active and savvy across social media sites

Industry/Entity Type

Events

Number of Pages Required

3 page

Font styles to use
Other font styles liked:
• Phi Roman

Requirements
Must have
• Each event offering runs for a limited time so a countdown timer is also to be included as well as a counter of number of participants (please find example attached).
• The interface needs to have the options for 'Live 'Music', 'Nightlife', 'Festivals', 'Comedy' and 'Everything Else'. Also
• A 'featured' section, for our promoted events
• Social sharing icons for Chatterbox, Flitter, PingTalk, SMS and Email
• Room the inclusion of a video
• Pages for clients to sign up - registering details ect.
• Content is still being completed, so room available to add when ready
Nice to have
• An interface design we like as a guiding templates on is https://quorvaapp.com/
• Luma wordpress theme is also of interest.
• Scroll over clicking for main interface and also for the event once clicked upon.
• Event pages similar desgin to quorva with same features such as Google Maps but also participant counter and affiliate marketing options.
Should not have
• CMS no longer necessary

```html
<!DOCTYPE html>
<html lang="en">
<head>
<meta charset="utf-8">
<title>Bandwise — Events</title>
<link href="https://fonts.googleapis.com/css2?family=Open+Sans:wght@400;600;700;800&family=Oswald:wght@500&display=swap" rel="stylesheet">
<style>
:root{
  --navy:#14233a;
  --navy-deep:#0f1b2e;
  --orange:#f15a22;
  --orange-dark:#d94a15;
  --grey-bg:#e4e7eb;
  --text:#4a4f57;
  --muted:#8a9099;
  --white:#ffffff;
}
*{box-sizing:border-box;margin:0;padding:0}
html,body{width:1200px;height:2196px;overflow:hidden}
body{font-family:"Open Sans",Arial,sans-serif;color:var(--text);background:var(--white);position:relative}

/* header */
.site-header{height:64px;background:var(--navy);display:flex;align-items:center;justify-content:space-between;padding:0 40px 0 24px}
.brand{display:flex;align-items:center;gap:10px;color:var(--white);font-weight:700;font-size:24px;letter-spacing:1px;text-transform:uppercase}
.brand-mark{width:30px;height:30px;background:var(--orange)}
.main-nav{display:flex;height:64px}
.main-nav a{color:var(--white);text-decoration:none;font-size:15px;padding:0 22px;display:flex;align-items:center}
.main-nav a.active{background:var(--orange)}

/* hero */
.hero{height:506px;position:relative;background:linear-gradient(180deg,#0c1a3a 0%,#1c2f63 40%,#3a3b5c 70%,#5a4630 100%);text-align:center;color:var(--white)}
.hero-photo{position:absolute;inset:0;background:radial-gradient(ellipse 260px 220px at 240px 240px,rgba(60,110,255,.45),transparent 70%),radial-gradient(ellipse 500px 90px at 700px 430px,rgba(255,170,70,.35),transparent 70%)}
.hero-content{position:relative;padding-top:14px}
.hero-date{display:inline-block;font-size:28px;font-weight:400;padding:0 20px 4px;border-bottom:2px solid rgba(255,255,255,.8)}
.hero-title{font-family:"Oswald","Open Sans",sans-serif;font-weight:500;font-size:44px;letter-spacing:1px;margin-top:8px}
.btn{display:inline-block;font-size:16px;font-weight:600;color:var(--white);border:none;padding:10px 26px;border-radius:2px}
.btn-orange{background:var(--orange)}
.btn-dark{background:var(--navy)}
.hero .btn{margin-top:14px}

/* intro */
.intro{height:260px;position:relative;padding:28px 88px 0}
.intro-icon{position:absolute;left:88px;top:40px;width:40px;height:40px;background:var(--orange);border-radius:3px}
.intro-body{margin-left:56px;width:560px}
.intro-title{color:var(--navy);font-size:20px;font-weight:800;text-transform:uppercase;line-height:1.2;padding-top:8px}
.intro-sub{color:var(--orange);font-size:11px;font-weight:600;margin:2px 0 10px}
.intro-body p{font-size:11px;line-height:1.55;color:var(--muted);margin-bottom:8px}
.intro-actions{display:flex;gap:22px;margin-top:12px}
.intro-actions .btn{padding:9px 34px}
.crowd{position:absolute;right:88px;top:36px;width:370px;height:140px;background:linear-gradient(0deg,#1a1a1a 0%,#555 45%,#f2f2f2 100%)}

/* categories */
.categories{height:440px;background:var(--orange);padding:50px 88px 0;position:relative}
.category-list{display:flex;gap:20px}
.category-card{width:241px;height:260px;background:var(--white);border-radius:2px;overflow:hidden}
.category-photo{height:140px}
.ph-live{background:linear-gradient(160deg,#1a1a2e,#7a7a90 60%,#2a2a3a)}
.ph-night{background:linear-gradient(160deg,#3a1c3e,#b45a6a 55%,#2a1230)}
.ph-fest{background:linear-gradient(160deg,#6a86b8,#c9a77b 55%,#5a4a3a)}
.ph-comedy{background:linear-gradient(160deg,#9aa0a8,#d8c4b0 55%,#6a6e74)}
.category-info{padding:10px 12px}
.category-name{color:var(--navy);font-size:16px;font-weight:700}
.category-info p{font-size:11px;color:var(--muted);line-height:1.45;margin-top:4px;height:34px}
.category-meta{display:flex;justify-content:space-between;align-items:center;margin-top:10px;font-size:10px;color:var(--muted)}
.btn-small{background:var(--orange);color:var(--white);font-size:10px;padding:4px 10px;border-radius:2px}
.slider-arrows{display:flex;justify-content:center;gap:8px;margin-top:26px}
.arrow{width:34px;height:34px;background:var(--navy-deep);display:flex;align-items:center;justify-content:center}

/* featured */
.featured{height:810px;background:var(--grey-bg);padding:40px 88px 0}
.featured-panel{background:var(--white);height:740px;box-shadow:0 1px 4px rgba(0,0,0,.12)}
.featured-head{height:60px;background:var(--navy);color:var(--white);font-size:20px;font-weight:700;text-transform:uppercase;display:flex;align-items:center;padding-left:22px}
.event-row{display:flex;align-items:center;height:220px;padding:0 28px}
.event-ring{width:150px;height:150px;position:relative;flex:none}
.event-ring svg{position:absolute;inset:0}
.ring-label{position:absolute;inset:0;display:flex;flex-direction:column;align-items:center;justify-content:center;color:var(--navy)}
.ring-label strong{font-size:38px;font-weight:700;line-height:1}
.ring-label span{font-size:11px;color:var(--muted)}
.event-card{margin-left:48px;width:780px;height:170px;background:var(--white);box-shadow:0 1px 6px rgba(0,0,0,.18);padding:20px 24px}
.event-top{display:flex;justify-content:space-between;align-items:center}
.event-title{color:var(--orange);font-size:16px;font-weight:600}
.participants{display:flex;align-items:center;gap:10px;color:var(--navy);font-weight:700;font-size:14px}
.participants b{width:40px;height:40px;border-radius:50%;background:var(--navy);color:var(--white);font-size:11px;display:flex;align-items:center;justify-content:center}
.event-card p{font-size:12px;line-height:1.6;color:var(--muted);margin-top:16px;width:520px}

/* footer */
.site-footer{height:116px;background:var(--navy);text-align:center;color:var(--white);padding-top:14px}
.social-links{display:flex;justify-content:center;gap:14px}
.social-links span{width:34px;height:34px;border-radius:50%;background:var(--navy-deep);border:1px solid rgba(255,255,255,.35);display:flex;align-items:center;justify-content:center}
.footer-nav{display:flex;justify-content:center;gap:48px;margin-top:16px;font-size:13px}
.copyright{font-size:11px;margin-top:10px;color:#c4cad3}
</style>
</head>
<body>

<header class="site-header">
  <div class="brand"><span class="brand-mark"></span>Bandwise</div>
  <nav class="main-nav">
    <a class="active">Home</a><a>About</a><a>Events</a><a>Schedule</a><a>Participants</a><a>Contact Us</a>
  </nav>
</header>

<section class="hero">
  <div class="hero-photo" role="img" aria-label="Night photo of a London riverside with a lit observation wheel"></div>
  <div class="hero-content">
    <div class="hero-date">1st January, 2015</div>
    <h1 class="hero-title">LOREM IPSUM IS SIMPLY DUMMY TEXT</h1>
    <span class="btn btn-orange">Registration</span>
  </div>
</section>

<section class="intro">
  <div class="intro-icon"></div>
  <div class="intro-body">
    <h2 class="intro-title">Contrary to popular belief, Lorem Ipsum is not simply</h2>
    <div class="intro-sub">The standard chunk of Lorem Ipsum used since the</div>
    <p>Lorem Ipsum is simply dummy text of the printing and typesetting industry. Lorem Ipsum has been the industry's standard dummy text ever since the 1500s, when an unknown printer took a galley of type and scrambled it to make a type specimen book.</p>
    <p>Contrary to popular belief, Lorem Ipsum is not simply random text. It has roots in a piece of classical Latin literature from 45 BC, making it over 2000 years old, and a Latin professor looked it up.</p>
    <div class="intro-actions"><span class="btn btn-orange">Sign Up</span><span class="btn btn-dark">Watch Video</span></div>
  </div>
  <div class="crowd" role="img" aria-label="Silhouette of a concert crowd with raised hands"></div>
</section>

<section class="categories">
  <div class="category-list">
    <article class="category-card">
      <div class="category-photo ph-live" role="img" aria-label="Live music concert stage"></div>
      <div class="category-info">
        <div class="category-name">Live 'Music</div>
        <p>Lorem Ipsum is simply dummy text of the printing and typesetting</p>
        <div class="category-meta"><span>30 September</span><span class="btn-small">Register</span></div>
      </div>
    </article>
    <article class="category-card">
      <div class="category-photo ph-night" role="img" aria-label="Nightlife club scene"></div>
      <div class="category-info">
        <div class="category-name">Nightlife</div>
        <p>Lorem Ipsum is simply dummy text of the printing and typesetting</p>
        <div class="category-meta"><span>30 September</span><span class="btn-small">Register</span></div>
      </div>
    </article>
    <article class="category-card">
      <div class="category-photo ph-fest" role="img" aria-label="Outdoor festival crowd"></div>
      <div class="category-info">
        <div class="category-name">Festivals</div>
        <p>Lorem Ipsum is simply dummy text of the printing and typesetting</p>
        <div class="category-meta"><span>30 September</span><span class="btn-small">Register</span></div>
      </div>
    </article>
    <article class="category-card">
      <div class="category-photo ph-comedy" role="img" aria-label="Comedy performer on stage"></div>
      <div class="category-info">
        <div class="category-name">Comedy</div>
        <p>Lorem Ipsum is simply dummy text of the printing and typesetting</p>
        <div class="category-meta"><span>30 September</span><span class="btn-small">Register</span></div>
      </div>
    </article>
  </div>
  <div class="slider-arrows">
    <span class="arrow"><svg width="12" height="12" viewBox="0 0 12 12"><path d="M8 1 3 6l5 5" fill="none" stroke="#fff" stroke-width="2"/></svg></span>
    <span class="arrow"><svg width="12" height="12" viewBox="0 0 12 12"><path d="M4 1l5 5-5 5" fill="none" stroke="#fff" stroke-width="2"/></svg></span>
  </div>
</section>

<section class="featured">
  <div class="featured-panel">
    <h2 class="featured-head">Featured Promoted Events</h2>

    <div class="event-row">
      <div class="event-ring">
        <svg viewBox="0 0 150 150"><circle cx="75" cy="75" r="62" fill="none" stroke="#e3e6ea" stroke-width="10"/><circle cx="75" cy="75" r="62" fill="none" stroke="#f15a22" stroke-width="10" stroke-dasharray="312 390" transform="rotate(-90 75 75)"/></svg>
        <div class="ring-label"><strong>120</strong><span>users</span></div>
      </div>
      <div class="event-card">
        <div class="event-top"><span class="event-title">Lorem Ipsum is simply dummy text of the printing.</span><span class="participants"><b>1000</b>Number of Participants</span></div>
        <p>Contrary to popular belief, Lorem Ipsum is not simply random text. It has roots in a piece of classical Latin literature from 45 BC, making it over 2000 years old and still in use today.</p>
      </div>
    </div>

    <div class="event-row">
      <div class="event-ring">
        <svg viewBox="0 0 150 150"><circle cx="75" cy="75" r="62" fill="none" stroke="#e3e6ea" stroke-width="10"/><circle cx="75" cy="75" r="62" fill="none" stroke="#f15a22" stroke-width="10" stroke-dasharray="175 390" transform="rotate(-90 75 75)"/></svg>
        <div class="ring-label"><strong>60</strong><span>users</span></div>
      </div>
      <div class="event-card">
        <div class="event-top"><span class="event-title">Lorem Ipsum is simply dummy text of the printing.</span><span class="participants"><b>1000</b>Number of Participants</span></div>
        <p>Contrary to popular belief, Lorem Ipsum is not simply random text. It has roots in a piece of classical Latin literature from 45 BC, making it over 2000 years old and still in use today.</p>
      </div>
    </div>

    <div class="event-row">
      <div class="event-ring">
        <svg viewBox="0 0 150 150"><circle cx="75" cy="75" r="62" fill="none" stroke="#e3e6ea" stroke-width="10"/><circle cx="75" cy="75" r="62" fill="none" stroke="#f15a22" stroke-width="10" stroke-dasharray="80 390" transform="rotate(-90 75 75)"/></svg>
        <div class="ring-label"><strong>20</strong><span>users</span></div>
      </div>
      <div class="event-card">
        <div class="event-top"><span class="event-title">Lorem Ipsum is simply dummy text of the printing.</span><span class="participants"><b>1000</b>Number of Participants</span></div>
        <p>Contrary to popular belief, Lorem Ipsum is not simply random text. It has roots in a piece of classical Latin literature from 45 BC, making it over 2000 years old and still in use today.</p>
      </div>
    </div>
  </div>
</section>

<footer class="site-footer">
  <div class="social-links">
    <span aria-label="Chatterbox"></span>
    <span aria-label="Flitter"></span>
    <span aria-label="PingTalk"></span>
    <span aria-label="SMS"><svg width="16" height="14" viewBox="0 0 16 14"><path d="M1 1h14v9H6l-4 3v-3H1z" fill="#fff"/></svg></span>
    <span aria-label="Email"><svg width="16" height="12" viewBox="0 0 16 12"><rect x="0.5" y="0.5" width="15" height="11" fill="#fff"/><path d="M1 1l7 6 7-6" fill="none" stroke="#14233a" stroke-width="1.4"/></svg></span>
  </div>
  <nav class="footer-nav"><span>Home</span><span>About</span><span>Events</span><span>Schedule</span><span>Participants</span><span>Contact Us</span></nav>
  <div class="copyright">Bandwise Copyright 2015</div>
</footer>

</body>
</html>
```